A private security company called "Tavron Security Services Ltd"

Hello everybody,

We need a web page for a company based in NZ. It is mainly an informative website so it would be wonderful if the designer puts their absolute best into making it a website that I would really appreciate. The website needs to show professionalism and also needs to make our web surfers find the information they need in a click. the company's colour is black and silver, and if those two colours could be integrated into the website it would be absolutely lovely. Please do contact me for any information.

Sincerely,
Dorian Vaskel

Industry/Entity Type

Security

```html
<!DOCTYPE html>
<html lang="en">
<head>
<meta charset="utf-8">
<title>Tavron Security Services Ltd</title>
<link rel="stylesheet" href="https://fonts.googleapis.com/css2?family=Pathway+Gothic+One&family=Arimo:wght@400;700&family=Cinzel:wght@600&display=swap">
<style>
:root{
  --ink:#1d1d1d;
  --text:#444;
  --muted:#8a8a8a;
  --light:#b9b9b9;
  --silver:#e9e9e9;
  --silver-2:#dcdcdc;
  --panel:#f4f4f4;
  --white:#fff;
  --footer-top:#5a5a5a;
  --footer-bottom:#2b2b2b;
  --footer-text:#9a9a9a;
}
*{margin:0;padding:0;box-sizing:border-box}
html,body{width:1200px;height:2748px;overflow:hidden}
body{position:relative;background:var(--white);font-family:"Arimo",Arial,sans-serif;color:var(--text)}
.abs{position:absolute}
.display{font-family:"Pathway Gothic One","Arial Narrow",sans-serif;color:var(--ink);font-weight:400}

/* header */
.site-header{left:0;top:0;width:1200px;height:157px;background:linear-gradient(#fafafa,#dedede)}
.brand{left:157px;top:40px;display:flex;align-items:center;gap:12px}
.brand-mark{width:26px;height:26px;border-radius:50%;background:var(--ink)}
.brand-name{font-family:"Arimo",Arial,sans-serif;font-weight:700;font-size:19px;color:var(--ink);line-height:1.15;width:170px}
.tagline{left:416px;top:26px;font-family:"Cinzel",serif;font-size:24px;color:var(--ink);letter-spacing:1px}
.main-nav{left:416px;top:100px;display:flex;gap:25px;font-size:13px;color:var(--ink);letter-spacing:.2px}
.social{display:flex;gap:9px}
.social span{width:30px;height:30px;border-radius:50%;background:#a7a7a7;display:block}
.header-social{left:932px;top:31px}

/* hero */
.hero{left:0;top:157px;width:1200px;height:517px;background:radial-gradient(ellipse at 45% 45%,#d9d2c6 0%,#8d8478 35%,#2e2a25 70%,#0f0d0b 100%)}
.slide-arrow{width:48px;height:48px;border-radius:50%;background:rgba(60,60,60,.75);display:flex;align-items:center;justify-content:center}
.hero-caption{left:0;top:536px;width:1200px;text-align:center;font-family:"Pathway Gothic One",sans-serif;color:var(--white);font-size:32px;line-height:46px;text-shadow:0 1px 3px rgba(0,0,0,.6)}
.hero-caption strong{font-weight:400;font-size:44px}

/* solutions */
.solutions{left:0;top:674px;width:1200px;height:711px;background:linear-gradient(#f3f3f3,#dcdcdc)}
.section-title{width:1200px;left:0;text-align:center;font-size:42px}
.services-side{left:157px;top:826px;width:210px}
.services-side h3{font-size:28px;margin-bottom:22px}
.services-side li{list-style:none;font-size:12.5px;color:var(--muted);padding-left:32px;position:relative;margin-bottom:21px;line-height:16px}
.services-side li::before{content:"";position:absolute;left:6px;top:3px;width:10px;height:10px;border-radius:50%;background:#cfcfcf}
.custom-box{left:157px;top:1096px;width:210px;height:253px;background:linear-gradient(#7a7a7a,#d6d6d6 55%,#9b9b9b);text-align:center;padding-top:26px}
.custom-box p{font-family:"Pathway Gothic One",sans-serif;font-size:26px;line-height:32px;color:var(--ink)}
.custom-box .brand-name{width:auto;margin-top:62px;font-size:17px}
.card-col{top:826px;width:222px;border-left:1px solid #c9c9c9}
.card{border-bottom:1px solid #c9c9c9;padding:14px 16px 0;position:relative;background:linear-gradient(#f6f6f6,#ececec)}
.card .thumb{height:90px;width:176px;border:5px solid var(--white);box-shadow:0 1px 3px rgba(0,0,0,.2);margin:0 auto}
.card h4{font-family:"Pathway Gothic One",sans-serif;font-weight:400;font-size:21px;color:var(--ink);margin:16px 0 6px}
.card p{font-size:11px;line-height:14px;color:var(--muted)}
.btn{display:inline-block;font-size:11px;color:var(--ink);background:linear-gradient(#fdfdfd,#dcdcdc);border:1px solid #c5c5c5;border-radius:3px;padding:6px 9px}
.card .btn{position:absolute;right:14px;bottom:12px}

/* industries */
.industries-title{top:1425px}
.industry{top:1532px;width:192px;text-align:center}
.industry .thumb{height:153px;border:4px solid var(--white);box-shadow:0 1px 4px rgba(0,0,0,.3)}
.industry span{display:block;margin-top:10px;font-family:"Pathway Gothic One",sans-serif;font-size:21px;color:var(--ink)}
.small-arrow{width:32px;height:32px;border-radius:50%;background:#b5b5b5;display:flex;align-items:center;justify-content:center}

/* residential / commercial */
.split{left:0;top:1787px;width:1200px;height:481px;background:linear-gradient(#fbfbfb,#ededed)}
.split-divider{left:598px;top:1810px;width:4px;height:420px;background:linear-gradient(90deg,rgba(0,0,0,.06),rgba(0,0,0,0))}
.split-item{top:1858px;width:420px;text-align:center}
.split-item .avatar{width:176px;height:176px;border-radius:50%;margin:0 auto;border:8px solid var(--silver-2)}
.split-item h4{font-family:"Pathway Gothic One",sans-serif;font-weight:400;font-size:22px;color:var(--ink);margin:14px 0 8px}
.split-item p{font-size:12px;line-height:14px;color:var(--light);width:350px;margin:0 auto 18px}
.split-item .btn{padding:7px 22px;font-size:12px}

/* footer */
.site-footer{left:0;top:2268px;width:1200px;height:480px;background:radial-gradient(ellipse at 50% 0%,var(--footer-top),var(--footer-bottom) 70%)}
.footer-col{top:2325px;color:var(--footer-text);font-size:12px;line-height:14px}
.footer-col h3{font-family:"Pathway Gothic One",sans-serif;font-weight:400;font-size:30px;color:var(--white);margin-bottom:40px}
.footer-col p{margin-bottom:14px}
.quick-links li{list-style:none;padding-left:20px;position:relative;margin-bottom:18px;font-size:11px;text-transform:uppercase;line-height:13px}
.quick-links li::before{content:"›";position:absolute;left:0;top:-3px;font-size:16px;color:var(--white)}
.contact-name{font-weight:700;font-size:11px;letter-spacing:1px;text-transform:uppercase;margin-bottom:22px!important}
.contact-row{display:flex;gap:12px;align-items:flex-start;font-size:11px;margin-bottom:18px}
.contact-row svg{flex:none}
.footer-rule{left:157px;top:2655px;width:886px;height:1px;background:#444;box-shadow:0 1px 0 #5a5a5a}
.copyright{left:157px;top:2694px;font-size:11px;color:var(--footer-text)}
.footer-social{left:926px;top:2684px}
.footer-social span{background:#8a8a8a}
</style>
</head>
<body>

<header class="site-header abs">
  <div class="brand abs"><span class="brand-mark"></span><span class="brand-name">Tavron Security Services Ltd</span></div>
  <div class="tagline abs">Standard of Vigilance</div>
  <nav class="main-nav abs"><span>HOME</span><span>ABOUT US</span><span>OUR SECURITY SOLUTIONS</span><span>INDUSTRIES WE SERVE</span><span>CONTACT US</span></nav>
  <div class="social header-social abs"><span></span><span></span><span></span></div>
</header>

<section class="hero abs" role="img" aria-label="Photo of a person looking through binoculars, sepia toned"></section>
<div class="slide-arrow abs" style="left:106px;top:392px"><svg width="14" height="22" viewBox="0 0 14 22"><path d="M11 2 3 11l8 9" fill="none" stroke="#fff" stroke-width="2"/></svg></div>
<div class="slide-arrow abs" style="left:1046px;top:392px"><svg width="14" height="22" viewBox="0 0 14 22"><path d="M3 2l8 9-8 9" fill="none" stroke="#fff" stroke-width="2"/></svg></div>
<div class="hero-caption abs"><strong>Private Investigation</strong> is simply dummy text of<br>the printing and typesetting industry.</div>

<section class="solutions abs"></section>
<h2 class="section-title display abs" style="top:722px">Our Security Solutions</h2>
<aside class="services-side abs">
  <h3 class="display">Services</h3>
  <ul>
    <li>Property guards</li>
    <li>Corporate events security</li>
    <li>Personal bodyguard for high net worth individuals</li>
    <li>Security consultancy</li>
    <li>Private investigation</li>
  </ul>
</aside>
<div class="custom-box abs">
  <p>CUSTOM OPTIONS<br>AVAILABLE</p>
  <div class="brand-name">Tavron Security<br>Services Ltd.</div>
</div>

<div class="card-col abs" style="left:377px">
  <article class="card" style="height:249px">
    <div class="thumb" role="img" aria-label="Photo of a model house" style="background:linear-gradient(#7d8a96,#8a5a3a 60%,#a46a3c)"></div>
    <h4>Property Guards</h4>
    <p>Lorem ipsum dolor sit amet, cons ectetuer adipiscing elit, sed diam nonummy nibh.</p>
    <span class="btn">Read More</span>
  </article>
  <article class="card" style="height:310px">
    <div class="thumb" role="img" aria-label="Photo of a security team at an event" style="background:linear-gradient(#3b4656,#1a2130)"></div>
    <h4>Corporate Events Security</h4>
    <p>Lorem ipsum dolor sit amet, cons ectetuer adipiscing elit, sed diam nonummy nibh euismod tincidunt ut laoreet dolore.</p>
    <span class="btn">Read More</span>
  </article>
</div>

<div class="card-col abs" style="left:599px">
  <article class="card" style="height:267px">
    <div class="thumb" role="img" aria-label="Photo of a bodyguard in a dark suit" style="background:linear-gradient(#2d3440,#10141b)"></div>
    <h4>Personal Bodyguards</h4>
    <p>Duis autem vel eum iriure dolor i n hendrerit in vulputate velit esse molestie consequat.</p>
    <span class="btn">Read More</span>
  </article>
  <article class="card" style="height:292px">
    <div class="thumb" role="img" aria-label="Photo of a business meeting" style="background:linear-gradient(#8d96a0,#4a525c)"></div>
    <h4>Security Consultancy</h4>
    <p>Duis autem vel eum iriure dolor in hendrerit in vulputate velit ess e molestie consequat, vel illum d olore eu feugiat nulla.</p>
    <span class="btn">Read More</span>
  </article>
</div>

<div class="card-col abs" style="left:821px;border-right:1px solid #c9c9c9">
  <article class="card" style="height:230px">
    <div class="thumb" role="img" aria-label="Photo of an investigator with a camera in a car" style="background:linear-gradient(#aab3bb,#3d434a)"></div>
    <h4>Private Investigation</h4>
    <p>Ut wisi enim ad minim veniam, qu is nostrud exerci tation ullamcorp er suscipit lobortis.</p>
    <span class="btn">Read More</span>
  </article>
  <article class="card" style="height:329px">
    <div class="thumb" role="img" aria-label="Photo of protection officers beside a black vehicle" style="background:linear-gradient(#6c6f72,#1c1d1f)"></div>
    <h4>Executive Protection</h4>
    <p>Lorem ipsum dolor sit amet, cons ectetuer adipiscing elit, sed diam nonummy nibh euismod tincidunt ut laoreet dolore magna aliquam erat volutpat.</p>
    <span class="btn">Read More</span>
  </article>
</div>

<h2 class="section-title display industries-title abs">Industries We Serve</h2>
<div class="small-arrow abs" style="left:110px;top:1591px"><svg width="10" height="16" viewBox="0 0 10 16"><path d="M8 2 2 8l6 6" fill="none" stroke="#fff" stroke-width="2"/></svg></div>
<div class="small-arrow abs" style="left:1058px;top:1591px"><svg width="10" height="16" viewBox="0 0 10 16"><path d="M2 2l6 6-6 6" fill="none" stroke="#fff" stroke-width="2"/></svg></div>
<div class="industry abs" style="left:157px"><div class="thumb" role="img" aria-label="Photo of an airliner over an airport terminal" style="background:linear-gradient(#3f86c9,#9cc6e6 55%,#8c9aa3)"></div><span>Ports and Airports</span></div>
<div class="industry abs" style="left:389px"><div class="thumb" role="img" aria-label="Photo of a resort with sun umbrellas" style="background:linear-gradient(#5b8fc8,#c9b79a 50%,#7a5d3f)"></div><span>Tourism</span></div>
<div class="industry abs" style="left:619px"><div class="thumb" role="img" aria-label="Photo of a bank building facade" style="background:linear-gradient(#9fb8d4,#3f5f8a)"></div><span>Financial Institution</span></div>
<div class="industry abs" style="left:847px"><div class="thumb" role="img" aria-label="Photo of an excavator at a coal mine" style="background:linear-gradient(#5a5a58,#1e1e1d)"></div><span>Natural Resources</span></div>

<section class="split abs"></section>
<div class="split-divider abs"></div>
<div class="split-item abs" style="left:120px">
  <div class="avatar" role="img" aria-label="Photo of a homeowner at a door alarm keypad" style="background:linear-gradient(#d7c9b4,#8a6f56)"></div>
  <h4>Residential Solutions</h4>
  <p>Lorem ipsum dolor sit amet, consectetur adipiscing elit. Sed in porta ut mauris vitae accumsan. Ut bibendum condim Phasellus placerat lectus nec odio fermentum, non Proin nec ligula condimentum, aliquet nisi id,</p>
  <span class="btn">Read More</span>
</div>
<div class="split-item abs" style="left:659px">
  <div class="avatar" role="img" aria-label="Photo of a guard with a radio in front of office towers" style="background:linear-gradient(#8fb3d6,#1f2630)"></div>
  <h4>Commercial Solutions</h4>
  <p>Lorem ipsum dolor sit amet, consectetur adipiscing elit. Sed in porta ut mauris vitae accumsan. Ut bibendum condim Phasellus placerat lectus nec odio fermentum, non Proin nec ligula condimentum, aliquet nisi id,</p>
  <span class="btn">Read More</span>
</div>

<footer class="site-footer abs"></footer>
<div class="footer-col abs" style="left:157px;width:302px">
  <h3>About us</h3>
  <p>Lorem ipsum dolor sit amet, consectetur adipiscing elit. Morbi pellentesque iaculis justo eget fermentum. Pellentesque commodo iaculis neque, vitae tincidunt odio pellentesque luctus. Aenean in eros eu magna vestibulum imperdiet pretium nec augue.</p>
  <p>Etiam quis turpis enim. Vestibulum auctor id mauris vulputate consequat. Suspendisse potenti. Cras at imperdiet elit. Integer fringilla tellus non diam condimentum, sed ultricies urna ultricies. Sed cong dui quis dui convallis dictum. Donec malesuada vulputate risus vitae vulputate. Maecenas in congue urna. Sed porttitor bibendum.</p>
</div>
<div class="footer-col abs" style="left:540px;width:130px">
  <h3>Quick Links</h3>
  <ul class="quick-links"><li>Home</li><li>About us</li><li>Our security solutions</li><li>Industries we serve</li><li>Contact us</li></ul>
</div>
<div class="footer-col abs" style="left:766px;width:290px">
  <h3>Contact Us</h3>
  <p class="contact-name">Tavron Security Services Ltd.</p>
  <div class="contact-row"><svg width="14" height="18" viewBox="0 0 14 18"><path d="M7 1a6 6 0 0 0-6 6c0 4.5 6 10 6 10s6-5.5 6-10a6 6 0 0 0-6-6z" fill="#fff"/><circle cx="7" cy="7" r="2.3" fill="#3a3a3a"/></svg><span>12 HARLOW STREET, KELBURY,<br>WELLINGTON 6021, NEW ZEALAND</span></div>
  <div class="contact-row"><svg width="14" height="16" viewBox="0 0 14 16"><path d="M3 1l3 3-2 2c1 2 3 4 5 5l2-2 3 3-2 3C7 15 0 8 1 3z" fill="#fff"/></svg><span>+64 4 555 0182</span></div>
  <div class="contact-row"><svg width="16" height="12" viewBox="0 0 16 12"><rect x="0" y="0" width="16" height="12" fill="#fff"/><path d="M0 0l8 6 8-6" fill="none" stroke="#3a3a3a" stroke-width="1.5"/></svg><span>info@tavronsecurity.co.nz</span></div>
</div>
<div class="footer-rule abs"></div>
<div class="copyright abs">Copyright © 2014 Tavron Security Service LTD.</div>
<div class="social footer-social abs"><span></span><span></span><span></span></div>

</body>
</html>
```